Book Title: Quiet Harbors -- Notes From a Restless Pulpit Today

I am looking for just the book cover design, do not need spine or back cover art.

This book is a memoir and the cover needs to be prepared for print and ebook applications.

The part of the title that follows the dash ("Notes From a Restless Pulpit Today") is not a subtitle but a tag and can be separated from the title itself.

I am inclined to a traditional design with "modern and minimalist" tendencies. I like graphic images that convey the idea of a "journey" or "quest". The memoir is about my pastoral work as a Christian minister but it is not a "religious" book. I do not want churches or any traditional religious symbols on the cover. In fact this book is directed toward those who have little, if any, interest in organized religion of any kind and if that could somehow be captured in the cover art it would be useful.

I am attaching a file with some sample cover art designs that I like or do not like to help guide your thinking. I am open to your interpretation and creative thinking. This book is a labor of love and I want the cover art to reflect my deep thinking on the topic.

```html
<!DOCTYPE html>
<html lang="en">
<head>
<meta charset="utf-8">
<title>Quiet Harbors — Front Cover</title>
<link rel="stylesheet" href="https://fonts.googleapis.com/css2?family=Marcellus&family=Open+Sans:wght@400;700&display=swap">
<style>
  :root {
    --stage: #e8e8e8;
    --paper: #ffffff;
    --title-blue: #1d62ad;
    --tile-blue: #c3d4ee;
    --tile-aqua: #cfe9f2;
    --accent-green: #1f8a3c;
    --frame-teal: #2b8f83;
    --ink: #222222;
    --tag-ink: #333333;
  }
  html, body {
    margin: 0;
    padding: 0;
    width: 1200px;
    height: 2462px;
    overflow: hidden;
    background: var(--stage);
  }
  .front-cover {
    position: absolute;
    left: 100px;
    top: 473px;
    width: 1000px;
    height: 1516px;
    background: var(--paper);
    box-shadow: 0 6px 30px rgba(0,0,0,0.12);
    overflow: hidden;
  }
  .tile-field {
    position: absolute;
    left: 0; top: 0;
    width: 100%;
    height: 820px;
    background:
      linear-gradient(180deg, rgba(255,255,255,0) 0%, rgba(255,255,255,0.55) 50%, var(--paper) 100%),
      linear-gradient(90deg, var(--tile-blue) 0%, var(--tile-aqua) 40%, var(--tile-blue) 70%, var(--tile-aqua) 100%);
    opacity: 0.6;
  }
  .journey-mark {
    position: absolute;
    left: 350px;
    top: 390px;
    width: 300px;
    height: 200px;
    background: radial-gradient(ellipse at center, rgba(31,138,60,0.85) 0%, rgba(31,138,60,0.45) 45%, rgba(31,138,60,0) 72%);
  }
  .title-block {
    position: absolute;
    left: 0;
    top: 590px;
    width: 100%;
    margin: 0;
    text-align: center;
    font-family: "Marcellus", serif;
    font-weight: 400;
    color: var(--title-blue);
    line-height: 1.12;
  }
  .title-line {
    display: block;
    font-size: 145px;
    letter-spacing: -2px;
  }
  .tagline {
    position: absolute;
    left: 50%;
    top: 955px;
    margin: 0;
    transform: translateX(-50%);
    white-space: nowrap;
    border: 2px solid var(--frame-teal);
    padding: 6px 14px;
    font-family: "Open Sans", sans-serif;
    font-size: 32px;
    color: var(--tag-ink);
  }
  .tagline strong { font-weight: 700; }
  .author-rule {
    position: absolute;
    left: 460px;
    top: 1125px;
    width: 80px;
    height: 4px;
    background: var(--frame-teal);
  }
  .author-name {
    position: absolute;
    left: 0;
    top: 1160px;
    width: 100%;
    margin: 0;
    text-align: center;
    font-family: "Open Sans", sans-serif;
    font-size: 74px;
    color: var(--ink);
  }
</style>
</head>
<body>
  <main class="front-cover">
    <div class="tile-field" role="img" aria-label="Scattered pale blue and aqua square tiles fading downward"></div>
    <div class="journey-mark" role="img" aria-label="Green branching arrows suggesting a journey"></div>
    <h1 class="title-block">
      <span class="title-line">QUIET</span>
      <span class="title-line">HARBORS</span>
    </h1>
    <p class="tagline">Notes From a Restless Pulpit <strong>Today</strong></p>
    <div class="author-rule"></div>
    <p class="author-name">Author Name</p>
  </main>
</body>
</html>
```